Unternehmen für Ordnung und Sauberkeit am Arbeitsplatz und Produkte zur Produktionsoptimierung benötigt Visitenkarten und Briefpapier
Zielgruppe
Produkte für Ordnung und Sauberkeit am Arbeitsplatz, Organisation von Arbeitsplätzen, Produkte zur Vereinfachung von Arbeitsabläufen, Produkte zur Produktionsoptimierung unter dem Lean Gedanke, Schlagwort: "5S", nachhaltig, sauber
Aufgabenstellung
Wir sind auf der Suche nach Visitenkarten und Briefpapier für das Unternehmen yourTidor. Nachhaltig, Sauber usw.. Unser Firmenlogo finden Sie anbei.

```html
<!DOCTYPE html>
<html lang="de">
<head>
<meta charset="utf-8">
<title>yourTidor – Visitenkarte</title>
<link rel="stylesheet" href="https://fonts.googleapis.com/css2?family=PT+Sans:wght@400;700&display=swap">
<style>
  :root {
    --stage: #b3b3b3;
    --paper: #ffffff;
    --brand-green: #1e8442;
    --ink: #2b2b2b;
    --ink-soft: #3a3a3a;
    --on-green: #ffffff;
  }
  * { margin: 0; padding: 0; box-sizing: border-box; }
  html, body {
    width: 1163px; height: 1200px; overflow: hidden;
    background: var(--stage);
    font-family: "PT Sans", sans-serif;
  }
  .canvas { position: relative; width: 1163px; height: 1200px; }

  .card { position: absolute; width: 727px; height: 417px; overflow: hidden; }

  .card-front { left: 156px; top: 200px; background: var(--paper); }
  .card-front .brand {
    position: absolute; left: 48px; top: 78px;
    display: flex; align-items: center; gap: 16px;
  }
  .brand-square { width: 56px; height: 56px; border-radius: 8px; background: var(--brand-green); }
  .brand-name { font-weight: 700; font-size: 58px; line-height: 1; color: var(--brand-green); }

  .person { position: absolute; right: 281px; top: 180px; text-align: right; }
  .person-name { font-weight: 700; font-size: 22px; color: var(--ink); line-height: 1.1; }
  .person-role { font-size: 16px; color: var(--ink-soft); margin-top: 10px; }

  .divider { position: absolute; left: 471px; top: 178px; width: 3px; height: 199px; background: var(--brand-green); }

  .contact { position: absolute; left: 498px; list-style: none; font-size: 17px; color: var(--ink); line-height: 23px; }
  .contact li { display: flex; align-items: center; }
  .contact svg { width: 14px; height: 14px; margin-right: 14px; fill: var(--brand-green); flex: none; }
  .contact .spacer { width: 14px; margin-right: 14px; flex: none; }
  .contact-address { top: 187px; }
  .contact-online { top: 263px; }
  .contact-phone { top: 331px; }

  .front-band { position: absolute; left: 0; bottom: 0; width: 100%; height: 15px; background: var(--brand-green); }

  .card-back { left: 287px; top: 676px; width: 724px; height: 415px; background: var(--brand-green); }
  .card-back .brand {
    position: absolute; left: 0; right: 0; top: 178px;
    display: flex; justify-content: center; align-items: center; gap: 18px;
  }
  .card-back .brand-square { background: var(--on-green); width: 62px; height: 62px; }
  .card-back .brand-name { color: var(--on-green); font-size: 64px; }
</style>
</head>
<body>
<main class="canvas">

  <section class="card card-front" aria-label="Visitenkarte Vorderseite">
    <div class="brand">
      <span class="brand-square"></span>
      <span class="brand-name">yourTidor</span>
    </div>

    <div class="person">
      <p class="person-name">Jonas Feldmann</p>
      <p class="person-role">Geschäftsführer</p>
    </div>

    <div class="divider"></div>

    <ul class="contact contact-address">
      <li><svg viewBox="0 0 14 14"><path d="M7 0C4.2 0 2.2 2 2.2 4.7 2.2 8 7 14 7 14s4.8-6 4.8-9.3C11.8 2 9.8 0 7 0zm0 6.6a1.9 1.9 0 110-3.8 1.9 1.9 0 010 3.8z"/></svg>Lindenweg 12</li>
      <li><span class="spacer"></span>79100 Talheim</li>
    </ul>

    <ul class="contact contact-online">
      <li><svg viewBox="0 0 14 14"><path d="M1 3h12v8H1z M1 3l6 4.5L13 3" fill="var(--brand-green)"/><path d="M1.5 3.5L7 7.6l5.5-4.1" fill="none" stroke="#fff" stroke-width="1"/></svg>info@tidor-mail.de</li>
      <li><svg viewBox="0 0 14 14"><circle cx="7" cy="7" r="6" fill="none" stroke="var(--brand-green)" stroke-width="1.2"/><ellipse cx="7" cy="7" rx="2.6" ry="6" fill="none" stroke="var(--brand-green)" stroke-width="1.1"/><path d="M1 7h12" stroke="var(--brand-green)" stroke-width="1.1"/></svg>www.tidor-web.de</li>
    </ul>

    <ul class="contact contact-phone">
      <li><svg viewBox="0 0 14 14"><path d="M1 5c0-2 2.5-3 6-3s6 1 6 3v1H9.5V4.5h-5V6H1z"/><path d="M3.5 7l1.5-2h4l1.5 2v5h-7z"/></svg>0 12 34 / 56 78 90</li>
      <li><svg viewBox="0 0 14 14"><path d="M3.5 1h7v4h-7z"/><path d="M1 6h12v5h-2V9H3v2H1z"/><path d="M4 10h6v3H4z"/></svg>0 12 34 / 56 78 911</li>
    </ul>

    <div class="front-band"></div>
  </section>

  <section class="card card-back" aria-label="Visitenkarte Rückseite">
    <div class="brand">
      <span class="brand-square"></span>
      <span class="brand-name">yourTidor</span>
    </div>
  </section>

</main>
</body>
</html>
```